Business Card Design

We have recently seen two business cards that caught our attention and think the designs would work for us. We are an accounting firm that serves small businesses in a variety of industries. Attached are the two business card that inspired us along with very rough layouts. We would like to see a professional layout using our company information.

Industry/Entity Type

Accounting

Contact Information for Business Card

Company Name - Marlowe Thistle
Address - 4182 Orlanby Lane, Suite 610, Houston, TX 77093
713-555-0187 - Main
281-555-0342 - Fax

Team Member Names, emails and phone numbers (see attachment)

```html
<!DOCTYPE html>
<html lang="en">
<head>
<meta charset="utf-8">
<title>Marlowe Thistle – Business Card</title>
<link rel="stylesheet" href="https://fonts.googleapis.com/css2?family=Cinzel:wght@500&family=Open+Sans:wght@400;600;700&display=swap">
<style>
  :root {
    --page-bg: #e6e6e4;
    --card-light: #ffffff;
    --card-light-shade: #e4e4e4;
    --card-dark: #383838;
    --swoosh-mid: #8a8a8a;
    --swoosh-light: #b4b4b4;
    --ink: #2a2a2a;
    --ink-on-dark: #ffffff;
    --ink-soft-on-dark: #e2e2e2;
  }
  * { margin: 0; padding: 0; box-sizing: border-box; }
  html, body {
    width: 1200px; height: 900px; overflow: hidden;
    background: var(--page-bg);
  }
  .canvas { position: relative; width: 1200px; height: 900px; }
  .business-card {
    position: absolute; left: 100px; top: 164px;
    width: 1000px; height: 571px;
    border-radius: 48px; overflow: hidden;
    box-shadow: 0 10px 30px rgba(0,0,0,0.18);
  }
  .card-art { position: absolute; inset: 0; width: 100%; height: 100%; }
  .brand {
    position: absolute; left: 390px; top: 120px;
    display: flex; flex-direction: column; align-items: center; gap: 22px;
  }
  .brand-dot {
    width: 58px; height: 58px; border-radius: 50%;
    background: var(--ink);
  }
  .brand-name {
    font-family: "Cinzel", serif; font-weight: 500;
    font-size: 42px; letter-spacing: 1px; color: var(--ink);
    white-space: nowrap;
  }
  .person {
    position: absolute; right: 48px; top: 318px; text-align: right;
    font-family: "Open Sans", sans-serif; color: var(--ink-on-dark);
  }
  .person-name { font-weight: 700; font-size: 26px; line-height: 1.2; }
  .person-title { font-weight: 400; font-size: 22px; color: var(--ink-soft-on-dark); }
  .contact-list {
    position: absolute; left: 62px; top: 404px; list-style: none;
    font-family: "Open Sans", sans-serif; font-size: 15px;
    color: var(--ink-on-dark); line-height: 1.25;
  }
  .contact-item { display: flex; align-items: flex-start; gap: 9px; margin-bottom: 2px; }
  .contact-item.address { margin-bottom: 6px; }
  .contact-icon { flex: none; width: 15px; height: 15px; margin-top: 2px; }
</style>
</head>
<body>
<main class="canvas">
  <section class="business-card" aria-label="Marlowe Thistle business card">
    <svg class="card-art" viewBox="0 0 1000 571" preserveAspectRatio="none" aria-hidden="true">
      <defs>
        <linearGradient id="cardLight" x1="0" y1="0" x2="0.4" y2="1">
          <stop offset="0" stop-color="var(--card-light)"/>
          <stop offset="1" stop-color="var(--card-light-shade)"/>
        </linearGradient>
      </defs>
      <rect width="1000" height="571" fill="url(#cardLight)"/>
      <path d="M20,372 C260,352 560,345 720,262 C820,210 870,130 930,62 C900,150 850,220 760,282 C600,380 300,370 20,372 Z" fill="var(--swoosh-light)"/>
      <path d="M430,362 C620,350 760,300 840,220 C900,160 930,110 960,80 C950,150 920,210 860,262 C760,340 600,365 430,362 Z" fill="var(--swoosh-mid)"/>
      <path d="M0,392 C260,395 590,388 760,306 C860,258 920,190 1000,150 L1000,571 L0,571 Z" fill="var(--card-dark)"/>
    </svg>

    <div class="brand">
      <span class="brand-dot"></span>
      <span class="brand-name">Marlowe Thistle</span>
    </div>

    <div class="person">
      <p class="person-name">Dana Whitcombe</p>
      <p class="person-title">Owner / C.E.O</p>
    </div>

    <ul class="contact-list">
      <li class="contact-item address">
        <svg class="contact-icon" viewBox="0 0 16 16"><circle cx="8" cy="8" r="8" fill="#fff"/><path d="M8 3.5a3 3 0 0 0-3 3c0 2.2 3 6 3 6s3-3.8 3-6a3 3 0 0 0-3-3zm0 4.2a1.2 1.2 0 1 1 0-2.4 1.2 1.2 0 0 1 0 2.4z" fill="#383838"/></svg>
        <span>4182 Orlanby Lane, Suite 610,<br>Houston, TX 77093</span>
      </li>
      <li class="contact-item">
        <svg class="contact-icon" viewBox="0 0 16 16"><circle cx="8" cy="8" r="8" fill="#fff"/><path d="M5.2 4h1.6l.7 2-1 .8a5 5 0 0 0 2.7 2.7l.8-1 2 .7v1.6c0 .5-.4.8-.9.8A7 7 0 0 1 4.4 4.9c0-.5.3-.9.8-.9z" fill="#383838"/></svg>
        <span>713-555-0187</span>
      </li>
      <li class="contact-item">
        <svg class="contact-icon" viewBox="0 0 16 16"><circle cx="8" cy="8" r="8" fill="#fff"/><rect x="4.5" y="6" width="7" height="5" rx="1" fill="#383838"/><rect x="6" y="3.8" width="4" height="2.6" fill="#383838"/></svg>
        <span>281-555-0342</span>
      </li>
      <li class="contact-item">
        <svg class="contact-icon" viewBox="0 0 16 16"><circle cx="8" cy="8" r="8" fill="#fff"/><rect x="5.5" y="3.5" width="5" height="9" rx="1" fill="#383838"/></svg>
        <span>713-555-0219</span>
      </li>
      <li class="contact-item">
        <svg class="contact-icon" viewBox="0 0 16 16"><circle cx="8" cy="8" r="8" fill="#fff"/><rect x="4" y="5" width="8" height="6" rx="1" fill="#383838"/><path d="M4.5 5.5 8 8.3l3.5-2.8" stroke="#fff" stroke-width="1" fill="none"/></svg>
        <span>dana@marlowethistle.com</span>
      </li>
      <li class="contact-item">
        <svg class="contact-icon" viewBox="0 0 16 16"><circle cx="8" cy="8" r="8" fill="#fff"/><circle cx="8" cy="8" r="4.2" fill="none" stroke="#383838" stroke-width="1.1"/><path d="M3.8 8h8.4M8 3.8c-2 2.5-2 5.9 0 8.4M8 3.8c2 2.5 2 5.9 0 8.4" stroke="#383838" stroke-width="0.9" fill="none"/></svg>
        <span>www.marlowethistle.com</span>
      </li>
    </ul>
  </section>
</main>
</body>
</html>
```